Brindlewick Solutions Ltd

I'd like to create a company letterhead for the attached logo in word format.

I'd like to emphasis the icon in large translucent state from the left corner and ensure that the letterhead colouring matches the colour palette of the current logo with a contrast so it's clear to see. I've attached a copy of our sister company page on the app for reference.

```html
<!DOCTYPE html>
<html lang="en">
<head>
<meta charset="utf-8">
<title>Brindlewick Solutions Ltd – Letterhead</title>
<link href="https://fonts.googleapis.com/css2?family=Lato:wght@400;700&display=swap" rel="stylesheet">
<style>
  :root {
    --backdrop: #8c8c8c;
    --paper: #ffffff;
    --ink-dark: #111111;
    --brand-teal: #00b9a6;
    --text-light: #ffffff;
    --rule: #3a5f5a;
  }
  * { margin: 0; padding: 0; box-sizing: border-box; }
  html, body {
    width: 1061px; height: 1200px; overflow: hidden;
    background: var(--backdrop);
    font-family: "Lato", Arial, sans-serif;
  }
  .letterhead {
    position: absolute; left: 120px; top: 20px;
    width: 820px; height: 1160px;
    background: var(--paper);
    box-shadow: 0 2px 10px rgba(0,0,0,.25);
    overflow: hidden;
  }
  .page-shapes { position: absolute; inset: 0; width: 100%; height: 100%; }
  .brand {
    position: absolute; left: 61px; top: 70px;
    display: flex; align-items: center; gap: 10px;
  }
  .brand-dot {
    width: 44px; height: 44px; border-radius: 50%;
    background: var(--brand-teal);
  }
  .brand-name {
    color: var(--brand-teal); font-size: 30px; font-weight: 400;
    letter-spacing: .5px;
  }
  .header-rule {
    position: absolute; top: 70px; width: 1px; height: 58px;
    background: var(--rule);
  }
  .header-rule.first { left: 318px; }
  .header-rule.second { left: 530px; }
  .address, .contacts {
    position: absolute; top: 71px;
    font-size: 13.5px; line-height: 18px; color: var(--text-light);
  }
  .address { left: 354px; }
  .address .company { color: var(--brand-teal); }
  .contacts { left: 566px; }
  .contact-line { display: flex; align-items: center; gap: 6px; }
  .contact-line svg { width: 11px; height: 11px; fill: var(--brand-teal); }
  .website {
    position: absolute; left: 426px; top: 1115px;
    font-size: 12.5px; letter-spacing: 4.2px; color: var(--text-light);
  }
  .website strong { font-weight: 700; }
</style>
</head>
<body>
<main class="letterhead">
  <svg class="page-shapes" viewBox="0 0 1037 1467" preserveAspectRatio="none" aria-hidden="false">
    <defs>
      <radialGradient id="glow" cx="0.2" cy="0.75" r="0.9">
        <stop offset="0" stop-color="#eeeeee"/>
        <stop offset="0.6" stop-color="#f7f7f7"/>
        <stop offset="1" stop-color="#ffffff"/>
      </radialGradient>
    </defs>
    <g role="img" aria-label="Soft grey sunburst of light rays behind a faint brand circle">
      <rect x="0" y="520" width="1037" height="947" fill="url(#glow)"/>
      <circle cx="199" cy="1157" r="202" fill="#ffffff" opacity="0.8"/>
      <circle cx="199" cy="1157" r="162" fill="#f1f1f1"/>
    </g>
    <path class="header-band" fill="#111111"
      d="M0 0 H1037 V292 C930 225 860 204 740 204 C600 204 420 267 200 267 C110 267 50 250 0 225 Z"/>
    <path class="footer-band" fill="#00b9a6"
      d="M0 1382 C50 1407 110 1424 200 1424 C420 1424 600 1362 740 1362 C860 1362 930 1385 1037 1449 V1467 H0 Z"/>
  </svg>

  <div class="brand">
    <span class="brand-dot"></span>
    <span class="brand-name">Brindlewick</span>
  </div>

  <span class="header-rule first"></span>
  <address class="address" style="font-style:normal">
    <div class="company">Brindlewick Solutions Ltd</div>
    <div>4370 Harlow Lane</div>
    <div>Westbrook, CT 06498</div>
  </address>

  <span class="header-rule second"></span>
  <div class="contacts">
    <div class="contact-line">
      <svg viewBox="0 0 12 12"><path d="M2.5 0.5 L4.5 0.5 L5.2 3 L3.8 4 C4.4 5.5 6 7.2 7.8 8 L8.8 6.6 L11.5 7.3 L11.5 9.5 C11.5 10.6 10.6 11.5 9.5 11.5 C4.8 11.2 0.8 7.2 0.5 2.5 C0.5 1.4 1.4 0.5 2.5 0.5 Z"/></svg>
      <span>(555) 014-2291</span>
    </div>
    <div class="contact-line">
      <svg viewBox="0 0 12 12"><path d="M3 0.5 H9 V3.5 H3 Z M1 4 H11 C11.6 4 12 4.4 12 5 V9 H9.5 V11.5 H2.5 V9 H0 V5 C0 4.4 0.4 4 1 4 Z M3.5 7.5 V10.5 H8.5 V7.5 Z"/></svg>
      <span>(555) 014-2291</span>
    </div>
    <div class="contact-line">
      <svg viewBox="0 0 12 12"><path d="M0.5 2.5 H11.5 V9.5 H0.5 Z" fill="none" stroke="#00b9a6" stroke-width="1"/><path d="M0.5 2.5 L6 6.5 L11.5 2.5 Z"/></svg>
      <span>info@brindlewicksolutions.com</span>
    </div>
  </div>

  <div class="website">www.<strong>BrindlewickSolutions</strong>.com</div>
</main>
</body>
</html>
```